Executive Business Card for Healthcare Company [Need Today]

I need a business card design for a healthcare company. The only branding the company has thus far is a logo. The cards will be utilized by company executives. The design I envision will be vibrant and appealing but with a corporate feel. They shouldn't be too casual or playful. I would like to complete this project TODAY if possible.

Target Market(s)

Healthcare vendors, other executives in healthcare and pharmaceuticals

Industry/Entity Type

Pharmaceutical

Contact Information for Business Card

See attachment

Font styles to use
Serif
Sans Serif

Colors

Designer to choose colors to be used in the design.

```html
<!DOCTYPE html>
<html lang="en">
<head>
<meta charset="utf-8">
<title>Corvane Therapeutics – Business Card</title>
<link rel="stylesheet" href="https://fonts.googleapis.com/css2?family=Roboto:wght@300;400;500&display=swap">
<style>
  :root {
    --bg: #e8e9ea;
    --teal: #22abc2;
    --green: #4cb08a;
    --white: #ffffff;
    --paper: #f4f4f4;
    --brand: #2aa5a8;
    --curve-shadow: #c9cbcc;
  }
  html, body {
    margin: 0;
    padding: 0;
    overflow: hidden;
  }
  body {
    width: 1200px;
    height: 726px;
    background: var(--bg);
    font-family: "Roboto", Arial, sans-serif;
    position: relative;
  }
  .card {
    position: absolute;
    width: 520px;
    height: 297px;
    top: 214px;
    overflow: hidden;
    box-shadow: 0 6px 18px rgba(0,0,0,0.12);
  }
  .card--front {
    left: 50px;
    background: linear-gradient(170deg, var(--teal) 0%, var(--green) 100%);
    color: var(--white);
  }
  .card--back {
    left: 630px;
  }
  .front__name {
    position: absolute;
    left: 0;
    right: 0;
    top: 92px;
    text-align: center;
    font-weight: 300;
    line-height: 1;
  }
  .front__name-main {
    display: block;
    font-size: 56px;
    letter-spacing: 1px;
    text-transform: lowercase;
  }
  .front__name-sub {
    display: block;
    font-size: 28px;
    letter-spacing: 1px;
    margin-top: 4px;
    text-transform: lowercase;
  }
  .front__web {
    position: absolute;
    left: 0;
    right: 0;
    bottom: 38px;
    text-align: center;
    font-size: 13px;
    font-weight: 300;
    letter-spacing: 4px;
  }
  .back__art {
    position: absolute;
    inset: 0;
  }
  .back__brand {
    position: absolute;
    left: 22px;
    top: 78px;
    width: 200px;
    text-align: center;
    color: var(--brand);
    font-weight: 300;
    line-height: 1;
  }
  .back__mark {
    display: block;
    width: 58px;
    height: 58px;
    margin: 0 auto 14px;
    border: 2px solid var(--brand);
    border-radius: 50%;
    box-sizing: border-box;
  }
  .back__brand-main {
    display: block;
    font-size: 38px;
    text-transform: lowercase;
  }
  .back__brand-sub {
    display: block;
    font-size: 19px;
    margin-top: 3px;
    text-transform: lowercase;
  }
  .contact {
    position: absolute;
    left: 300px;
    top: 62px;
    color: var(--white);
  }
  .contact__name {
    font-size: 21px;
    font-weight: 500;
    margin: 0;
  }
  .contact__title {
    font-size: 10px;
    font-weight: 300;
    margin: 3px 0 14px;
  }
  .contact__list {
    list-style: none;
    margin: 0;
    padding: 0;
    font-size: 12px;
    font-weight: 300;
  }
  .contact__list li {
    display: flex;
    align-items: center;
    gap: 7px;
    height: 18px;
  }
  .contact__icon {
    width: 11px;
    height: 11px;
    flex: none;
  }
  .contact__address {
    margin-top: 6px;
    font-size: 12px;
    font-weight: 300;
    line-height: 18px;
  }
</style>
</head>
<body>

<section class="card card--front" aria-label="Card front">
  <div class="front__name">
    <span class="front__name-main">Corvane</span>
    <span class="front__name-sub">therapeutics</span>
  </div>
  <div class="front__web">www.corvanerx.com</div>
</section>

<section class="card card--back" aria-label="Card back">
  <svg class="back__art" width="520" height="297" viewBox="0 0 520 297" aria-hidden="true">
    <defs>
      <linearGradient id="backGradient" x1="0" y1="0" x2="0.2" y2="1">
        <stop offset="0" stop-color="#22abc2"/>
        <stop offset="1" stop-color="#4cb08a"/>
      </linearGradient>
    </defs>
    <rect width="520" height="297" fill="url(#backGradient)"/>
    <path d="M0 0 H230 Q318 150 262 297 H0 Z" fill="#c9cbcc"/>
    <path d="M0 0 H222 Q306 150 252 297 H0 Z" fill="#f4f4f4"/>
  </svg>

  <div class="back__brand">
    <span class="back__mark"></span>
    <span class="back__brand-main">Corvane</span>
    <span class="back__brand-sub">therapeutics</span>
  </div>

  <div class="contact">
    <h1 class="contact__name">Daniel Reyes</h1>
    <p class="contact__title">Senior Director of Marketing</p>
    <ul class="contact__list">
      <li>
        <svg class="contact__icon" viewBox="0 0 12 12" aria-hidden="true"><path d="M2 3.5 Q6 1 10 3.5 V5 H8 V4 H4 V5 H2 Z M3 6 H9 L10 10 H2 Z" fill="#fff"/></svg>
        555-210-4837
      </li>
      <li>
        <svg class="contact__icon" viewBox="0 0 12 12" aria-hidden="true"><rect x="3" y="0.5" width="6" height="11" rx="1" fill="none" stroke="#fff" stroke-width="1.2"/><circle cx="6" cy="9.5" r="0.8" fill="#fff"/></svg>
        555-318-6042
      </li>
      <li>
        <svg class="contact__icon" viewBox="0 0 12 12" aria-hidden="true"><circle cx="6" cy="6" r="5" fill="none" stroke="#fff" stroke-width="1.1"/><path d="M1 6 H11 M6 1 Q3 6 6 11 M6 1 Q9 6 6 11" fill="none" stroke="#fff" stroke-width="0.9"/></svg>
        dreyes@corvanerx.com
      </li>
    </ul>
    <div class="contact__address">
      118 Linden Avenue<br>
      Marlow, GA 30112
    </div>
  </div>
</section>

</body>
</html>
```